Clear Plastic Card Design

I am looking to have a business card designed from my logo icon. I am looking to match the style of a different business card I have attached in the files.
Looking for a card that is plastic, with layers of transparency in the shape of my logo icon (also attached in the files) - not a circle like the other card. The winning design will incorporate the red icon logo on the front and back and include the charity's name, "Light for the Weary Souls" in the same or similar font, as well as an email and phone number. For now, use the email: email@lightfortheweary-mail.org and the phone number 555-382-7194.
We like how the sample business card has transparency, partial and full opacity layers and a matching color scheme. Files will need to be in vector so that our business card printing company can work with it.
UPDATE:
We've some excellent designs in, thank you everyone! I got an early review from the owner, and he requested a minor redirect to find his perfect design. He wants the design to stand out by NOT being a rectangle. Try instead a circle, square, or best yet - something that falls in the outline of the logo icon, either fully or partially. Thank you, everyone!
Light for the Weary Souls text should be incorporated as well as a phone and email.

```html
<!DOCTYPE html>
<html lang="en">
<head>
<meta charset="utf-8">
<title>Light for the Weary Souls – Business Card</title>
<link rel="stylesheet" href="https://fonts.googleapis.com/css2?family=Arimo:wght@400&display=swap">
<style>
  :root {
    --backdrop: #e2e2e2;
    --card: #ffffff;
    --ink: #1a1a1a;
    --brand-red: #d4143a;
    --brand-red-deep: #c10f32;
    --brand-orange: #f26a1b;
    --icon-fill: #111111;
  }
  * { box-sizing: border-box; margin: 0; padding: 0; }
  html, body {
    width: 1175px;
    height: 1200px;
    overflow: hidden;
    background: var(--backdrop);
    font-family: "Arimo", Arial, sans-serif;
  }
  .business-card {
    position: absolute;
    left: 69px;
    top: 73px;
    width: 1037px;
    height: 1053px;
    background: var(--card);
    border-radius: 50px;
    overflow: hidden;
  }
  .card-shapes {
    position: absolute;
    inset: 0;
    width: 100%;
    height: 100%;
  }
  .corner-fill {
    position: absolute;
    width: 260px;
    height: 260px;
  }
  .corner-fill--top-left {
    left: 0;
    top: 0;
    background: linear-gradient(135deg, var(--brand-red) 0%, var(--brand-orange) 100%);
    clip-path: polygon(0 0, 100% 0, 0 100%);
  }
  .corner-fill--bottom-right {
    right: 0;
    bottom: 0;
    background: linear-gradient(315deg, var(--brand-red-deep) 0%, var(--brand-orange) 100%);
    clip-path: polygon(100% 0, 100% 100%, 0 100%);
  }
  .brand-name {
    position: absolute;
    right: 310px;
    top: 342px;
    font-size: 44px;
    font-weight: 400;
    line-height: 54px;
    color: var(--ink);
    text-align: right;
    white-space: nowrap;
  }
  .contact-list {
    position: absolute;
    left: 87px;
    top: 720px;
    list-style: none;
    font-size: 41px;
    line-height: 57px;
    color: var(--ink);
    white-space: nowrap;
  }
</style>
</head>
<body>
  <main class="business-card">
    <div class="corner-fill corner-fill--top-left" role="img" aria-label="Decorative red-to-orange corner accent"></div>
    <div class="corner-fill corner-fill--bottom-right" role="img" aria-label="Decorative red-to-orange corner accent"></div>

    <svg class="card-shapes" viewBox="0 0 451 458" preserveAspectRatio="none" aria-hidden="true">
      <rect class="brand-square" x="340" y="122" width="70" height="70" fill="var(--brand-red)"/>

      <g class="contact-icons">
        <g class="icon icon--phone">
          <circle cx="51" cy="283" r="12" fill="var(--icon-fill)"/>
          <path d="M45.5 276.5 l3 -1 2.2 4.2 -1.8 1.6 c0.9 2 2.5 3.6 4.4 4.5 l1.6 -1.8 4.2 2.2 -1 3 c-6 0.3 -12.9 -6.3 -12.6 -12.7 z" fill="#fff"/>
        </g>
        <g class="icon icon--email">
          <circle cx="81" cy="283" r="12" fill="var(--icon-fill)"/>
          <rect x="74" y="278" width="14" height="10" rx="1" fill="#fff"/>
          <path d="M74.5 278.5 L81 284 L87.5 278.5" fill="none" stroke="var(--icon-fill)" stroke-width="1.2"/>
        </g>
        <g class="icon icon--web">
          <circle cx="111" cy="283" r="12" fill="var(--icon-fill)"/>
          <circle cx="111" cy="283" r="7.5" fill="none" stroke="#fff" stroke-width="1.4"/>
          <ellipse cx="111" cy="283" rx="3.2" ry="7.5" fill="none" stroke="#fff" stroke-width="1.2"/>
          <line x1="103.5" y1="283" x2="118.5" y2="283" stroke="#fff" stroke-width="1.2"/>
        </g>
      </g>
    </svg>

    <h1 class="brand-name">Light for the<br>Weary Souls</h1>

    <ul class="contact-list">
      <li class="contact-phone">555-382-7194</li>
      <li class="contact-email">email@lightfortheweary-mail.org</li>
      <li class="contact-web">www.lightforthewearysouls.org</li>
    </ul>
  </main>
</body>
</html>
```